Hearthside Lending Relief

Please help us give our website a remake or a FACELIFT. It is not very good but it says what we need it to say. But the design is terrible.
I would like our new design font and logo to be used as the theme.

I also want more photos on the site.

I also want consistency with the pages so they look clean.

We want the professionals to do this, let's see what you got!

Thank you!
Updates

Project Deadline Extended
Reason: I can understand you want to be paid. So I will commit to the fee but I want you to have time to make a KICK ASS website for me dudes! Thanks

HI!  Just wanted to say thanks for your time on these.  A lot are great.  However the firefighters have nothing to do with Foreclosure.  We are saving peoples homes from the bank taking them and selling them.   I LOVE the house photos and the families on the website.  That is the direction we like.  THanks.

THANK U ALL FOR THE WORK!   I like a few ending in the numbers: 147  733  693  536  620  478  727  508     I will go over them and choose one soon.  Thank you.   You will be paid shortly. 

Requirements
Must have
• Bright, Upbeat photos. Color scheme should be in order. We like icons on the bottom. not just text.

```html
<!DOCTYPE html>
<html lang="en">
<head>
<meta charset="utf-8">
<title>Hearthside Lending Relief</title>
<link href="https://fonts.googleapis.com/css2?family=Signika:wght@400;600&family=Open+Sans:wght@400;600&display=swap" rel="stylesheet">
<style>
:root{
  --red:#e0222a;
  --red-dark:#b8141b;
  --red-light:#f0474c;
  --ink:#333333;
  --ink-soft:#555555;
  --navy:#1f3b5c;
  --hero-bg:#eeeeee;
  --footer-bg:#e9edf2;
  --field-bg:#e8eff6;
  --line:#c9d6e3;
  --white:#ffffff;
}
*{box-sizing:border-box;margin:0;padding:0}
html,body{width:1103px;height:1200px;overflow:hidden;background:var(--white)}
body{position:relative;font-family:"Open Sans",Arial,sans-serif;color:var(--ink)}
.abs{position:absolute}
.head-font{font-family:"Signika",Arial,sans-serif}

/* header */
.top-rule{left:0;top:0;width:1103px;height:4px;background:var(--navy)}
.header{left:0;top:4px;width:1103px;height:126px;background:linear-gradient(#ffffff,#f1f1f1)}
.brand{left:48px;top:32px;display:flex;align-items:center;gap:14px}
.brand-mark{width:66px;height:66px;border-radius:50%;background:var(--red)}
.brand-name{font-family:"Signika",Arial,sans-serif;font-weight:600;font-size:22px;line-height:24px;color:var(--red);text-transform:uppercase;width:200px}
.call{left:870px;top:50px;font-family:"Signika",Arial,sans-serif;color:var(--red)}
.call-label{font-size:19px;line-height:22px}
.call-number{font-size:28px;line-height:32px}

/* nav */
.nav{left:0;top:130px;width:1103px;height:53px;background:linear-gradient(#f0474c,#e0222a 45%,#c81a21);display:flex;border-bottom:1px solid var(--red-dark)}
.nav a{display:block;height:53px;line-height:53px;color:var(--white);text-decoration:none;font-size:14px;padding:0 36px;border-right:1px solid rgba(0,0,0,.12);box-shadow:1px 0 0 rgba(255,255,255,.15)}
.nav a:last-child{border-right:none;box-shadow:none}
.nav a.current{font-weight:600;padding:0 30px 0 51px}

/* hero */
.hero{left:0;top:183px;width:1103px;height:325px;background:linear-gradient(#f7f7f7,var(--hero-bg))}
.hero-title{left:84px;top:240px;font-family:"Signika",Arial,sans-serif;font-size:29px;color:var(--red)}
.hero-punch{left:84px;top:277px;font-family:"Signika",Arial,sans-serif;font-size:23px;color:var(--red)}
.hero-text{left:84px;top:312px;width:410px;font-family:"Signika",Arial,sans-serif;font-size:13px;line-height:22px;color:var(--ink)}
.btn-dark{display:inline-block;background:linear-gradient(#5b5b5b,#1f1f1f);color:var(--white);border-radius:5px;border:1px solid #111;box-shadow:0 2px 3px rgba(0,0,0,.3)}
.learn-more{left:84px;top:392px;width:114px;height:34px;line-height:32px;text-align:center;font-family:"Signika",Arial,sans-serif;font-size:15px}
.hero-frame{left:522px;top:201px;width:511px;height:287px;background:var(--white);box-shadow:0 1px 5px rgba(0,0,0,.25);border-radius:3px}
.hero-photo{left:528px;top:208px;width:499px;height:273px;background:linear-gradient(#c9dbea 0%,#e6e0d2 40%,#b89b7e 62%,#6f9a4e 100%)}
.arrow{top:286px}

/* welcome */
.welcome-title{left:34px;top:530px;font-family:"Signika",Arial,sans-serif;font-size:20px;color:var(--red)}
.welcome-title strong{font-weight:600}
.welcome-text{left:34px;top:565px;width:725px;font-size:11.2px;line-height:18.3px;color:var(--ink)}
.welcome-text p{margin-bottom:18px}

/* contact form */
.form-box{left:777px;top:520px;width:306px;height:378px;border:1px solid var(--line);border-radius:5px;background:var(--white)}
.form-head{left:778px;top:521px;width:304px;height:40px;border-bottom:1px solid var(--line);background:linear-gradient(#f4f7fa,#e9eef4);border-radius:5px 5px 0 0}
.form-title{left:796px;top:530px;font-family:"Signika",Arial,sans-serif;font-size:20px;color:var(--red)}
.field{width:271px;height:31px;background:var(--field-bg);border:1px solid #d3dde8;border-radius:5px;font-size:11.5px;color:var(--red);padding:8px 11px;box-shadow:0 2px 2px rgba(160,180,200,.35)}
.field-msg{height:111px}
.submit{left:800px;top:846px;width:104px;height:30px;line-height:28px;text-align:center;font-size:12px;font-weight:600}

/* footer */
.footer{left:0;top:926px;width:1103px;height:226px;background:var(--footer-bg)}
.divider{top:928px;width:1px;height:176px;background:#c7cfd8}
.foot-title{top:946px;font-family:"Signika",Arial,sans-serif;font-size:20px;color:var(--red)}
.link-list{list-style:none;font-size:12px;color:var(--ink-soft)}
.link-list li{height:30px}
.social li{display:flex;align-items:center;gap:11px}
.social-icon{width:22px;height:22px;border-radius:4px;background:#4a7fb5;flex:none}
.contact-info{left:604px;top:985px;font-family:"Signika",Arial,sans-serif;font-size:13.5px;line-height:25px;color:var(--ink-soft)}
.contact-info .org{font-size:15.5px;text-transform:uppercase}
.copyright{left:36px;top:1166px;font-size:11.5px;color:var(--ink-soft)}
</style>
</head>
<body>

<div class="abs top-rule"></div>
<header class="abs header"></header>
<div class="abs brand">
  <span class="brand-mark"></span>
  <span class="brand-name">Hearthside Lending Relief</span>
</div>
<div class="abs call">
  <div class="call-label">Call Us Now</div>
  <div class="call-number">877-555-0148</div>
</div>

<nav class="abs nav">
  <a class="current" href="#">Main</a>
  <a href="#">About Us</a>
  <a href="#">Services</a>
  <a href="#">Contact Us</a>
  <a href="#">Financing Options</a>
</nav>

<section class="abs hero"></section>
<svg class="abs arrow" style="left:22px" width="28" height="78" viewBox="0 0 28 78"><polyline points="26,2 2,39 26,76" fill="none" stroke="#e0222a" stroke-width="1.6"/></svg>
<svg class="abs arrow" style="left:1053px" width="28" height="78" viewBox="0 0 28 78"><polyline points="2,2 26,39 2,76" fill="none" stroke="#e0222a" stroke-width="1.6"/></svg>
<h1 class="abs hero-title" style="font-weight:400">Hearthside Lending Relief</h1>
<h2 class="abs hero-punch" style="font-weight:400">Punch line here goes here</h2>
<p class="abs hero-text">Brightpath Web Studio is a web service company, offering a wide range of services which range from designing and development, that is covering almost all the fields in the best possible way.</p>
<a class="abs btn-dark learn-more">learn more &#8250;</a>
<div class="abs hero-frame"></div>
<div class="abs hero-photo" role="img" aria-label="Smiling family of four standing in front of their brick two-storey home on a sunny day"></div>

<h2 class="abs welcome-title" style="font-weight:400">Welcome to&nbsp; <strong>HEARTHSIDE LENDING RELIEF</strong></h2>
<div class="abs welcome-text">
  <p>HEARTHSIDE LENDING RELIEF specializes in assisting homeowners who are in FORECLOSURE, by offering solid alternatives to losing your home in a Trustee Sale.&nbsp; Having your home foreclosed on can damage your credit for up to 7 years.&nbsp; Most foreclosures end with the home owner being evicted from their home, leaving them with no money, no place to live and without ample time to safely remove their possessions from their home.&nbsp; There is no need to have this happen to you.&nbsp; No matter what part of foreclosure process you are in, WE CAN HELP!</p>
  <p>If you have received a Notice of Default (NOD) or Notice of Trustee Sale (NTS), you have options.&nbsp; Contact us today to speak to one of our licensed specialist, and let us help you put this situation behind you.<br>We speak to hundreds of homeowners every day, we understand how frustrating this can be.&nbsp; Don't live in fear of what is to come.&nbsp; You have other options, please call or email us today and we will immediately put our specialist to work finding you a solution.</p>
  <p>Don't try to handle this frustrating situation by yourself.&nbsp; HEARTHSIDE LENDING RELIEF is a team of knowledgeable real estate professionals, we can offer you a better solution during this tough time.<br>HEARTHSIDE LENDING RELIEF&nbsp; has been assisting families in foreclosure for years.&nbsp; Our skill and integrity has earned us a reputation for fast, professional, courteous and thorough solutions.&nbsp; With over 50 years of real estate knowledge and experience HEARTHSIDE LENDING RELIEF is ready to assist you.</p>
</div>

<div class="abs form-box"></div>
<div class="abs form-head"></div>
<h3 class="abs form-title" style="font-weight:400">Contact Form</h3>
<div class="abs field" style="left:791px;top:578px">type your full name</div>
<div class="abs field" style="left:793px;top:624px">type your phone no.</div>
<div class="abs field" style="left:796px;top:671px">type your email address</div>
<div class="abs field field-msg" style="left:796px;top:720px">type your message</div>
<a class="abs btn-dark submit">SUBMIT NOW &#8250;</a>

<footer class="abs footer"></footer>
<div class="abs divider" style="left:308px"></div>
<div class="abs divider" style="left:568px"></div>

<h3 class="abs foot-title" style="left:42px;font-weight:400">Quick links</h3>
<ul class="abs link-list" style="left:43px;top:991px">
  <li>Main Page</li><li>About Our Company</li><li>Services</li><li>Financing Options</li>
</ul>
<ul class="abs link-list" style="left:187px;top:992px">
  <li>FAQ's</li><li>Contact Form</li><li>Contact Us</li>
</ul>

<h3 class="abs foot-title" style="left:351px;font-weight:400">Get in Touch</h3>
<ul class="abs link-list social" style="left:351px;top:987px">
  <li><span class="social-icon"></span>Connect with Chirpline</li>
  <li><span class="social-icon"></span>Get in touch with Friendhub</li>
  <li><span class="social-icon"></span>Stay on Friendhub</li>
  <li><span class="social-icon"></span>Connect with Searchly</li>
</ul>

<h3 class="abs foot-title" style="left:604px;font-weight:400">Contact Info</h3>
<div class="abs contact-info">
  <div class="org">Hearthside Lending Relief</div>
  <div>118 Harbor Lane, Suite 210</div>
  <div>Bayview, CA 90410</div>
  <div>877-555-0148</div>
</div>

<div class="abs copyright">&copy; 2012 Company Name&nbsp; |&nbsp; All right reserved</div>

</body>
</html>
```